Small Business Broker Business Card Design

A business card design for a small business brokerage, which is a financial service, not unlike real estate brokerage, but for small businesses such as laundromats, pizza shops, restaurants, cleaners etc. The designs should all be simple, more conservative in nature, using the colors and font of the logo. Again, think real estate Brokerage as a business context
Contact Information for Business Card
Name: Glen R. Harlow. Title: Small Business Advisor. Email: g.harlow@bayfieldcapitalworks.example. Mobile: (555) 274-3918. Office: (555) 806-2147. www.bayfieldcapitalworks.example

```html
<!DOCTYPE html>
<html lang="en">
<head>
<meta charset="UTF-8">
<title>Bayfield Capital Works – Business Card</title>
<link href="https://fonts.googleapis.com/css2?family=Montserrat:wght@400;500;700&display=swap" rel="stylesheet">
<style>
  :root {
    --navy: #1d3a6e;
    --navy-deep: #172f5c;
    --navy-light: #2f5290;
    --green: #7cc242;
    --ink: #1d3a6e;
    --paper: #ffffff;
    --stage: #2a2c31;
  }
  * { margin: 0; padding: 0; box-sizing: border-box; }
  html, body { width: 1200px; height: 900px; overflow: hidden; }
  body {
    background: var(--stage);
    font-family: "Montserrat", sans-serif;
    position: relative;
  }
  .card {
    position: absolute;
    left: 285px;
    width: 630px;
    height: 360px;
    border-radius: 22px;
    overflow: hidden;
  }
  .card--front { top: 50px; background: var(--paper); }
  .card--back { top: 490px; background: var(--navy); }

  .brand__row { display: flex; align-items: center; gap: 10px; }
  .brand__square { width: 14px; height: 14px; background: var(--green); flex: none; }
  .brand__name {
    font-weight: 700;
    font-size: 20px;
    letter-spacing: 0.5px;
    color: var(--navy);
    text-transform: uppercase;
    white-space: nowrap;
  }
  .brand__tagline {
    margin-top: 4px;
    font-weight: 700;
    font-size: 10px;
    letter-spacing: 0.8px;
    color: var(--green);
    text-transform: uppercase;
    white-space: nowrap;
  }

  /* front */
  .card--front .brand {
    position: absolute;
    right: 60px;
    top: 90px;
  }
  .card--front .brand__row { justify-content: flex-end; }
  .card--front .brand__tagline { text-align: right; }

  .person {
    position: absolute;
    left: 40px;
    top: 196px;
  }
  .person__name {
    font-weight: 700;
    font-size: 26px;
    line-height: 30px;
    color: var(--ink);
  }
  .person__title {
    font-weight: 500;
    font-size: 14px;
    color: var(--ink);
    margin-top: 2px;
  }
  .divider {
    position: absolute;
    left: 40px;
    right: 60px;
    top: 256px;
    height: 1.5px;
    background: var(--navy);
  }
  .contacts {
    position: absolute;
    left: 40px;
    top: 268px;
    list-style: none;
  }
  .contacts li {
    display: flex;
    align-items: center;
    gap: 10px;
    font-size: 13px;
    color: var(--ink);
    line-height: 20px;
    white-space: nowrap;
  }
  .contacts svg { width: 12px; height: 12px; fill: var(--navy); flex: none; }

  /* back */
  .back-texture {
    position: absolute;
    inset: 0;
    background: linear-gradient(200deg, var(--navy-light) 0%, var(--navy) 40%, var(--navy-deep) 100%);
  }
  .back-brand {
    position: absolute;
    inset: 0;
    display: flex;
    flex-direction: column;
    align-items: center;
    justify-content: center;
  }
  .back-brand .brand__name { color: #ffffff; font-size: 22px; }
  .back-brand .brand__tagline { text-align: center; }
</style>
</head>
<body>

<section class="card card--front" aria-label="Business card front">
  <div class="brand">
    <div class="brand__row">
      <span class="brand__square"></span>
      <span class="brand__name">Bayfield Capital Works, Inc</span>
    </div>
    <div class="brand__tagline">Trusted guidance for every business sale</div>
  </div>

  <div class="person">
    <div class="person__name">Glen R. Harlow</div>
    <div class="person__title">Small Business Advisor</div>
  </div>

  <div class="divider"></div>

  <ul class="contacts">
    <li>
      <svg viewBox="0 0 24 24"><path d="M3 9c0-3 4-5 9-5s9 2 9 5v2h-5V9c-2-1-6-1-8 0v2H3zM6 13h12l2 7H4z"/></svg>
      (555) 806-2147
    </li>
    <li>
      <svg viewBox="0 0 24 24"><path d="M6 2h4l2 5-3 2c1 3 3 5 6 6l2-3 5 2v4c0 2-2 3-4 3C9 21 3 15 3 6c0-2 1-4 3-4z"/></svg>
      (555) 274-3918
    </li>
    <li>
      <svg viewBox="0 0 24 24"><path d="M2 5h20v14H2zM3 6l9 7 9-7v2l-9 7-9-7z"/></svg>
      g.harlow@bayfieldcapitalworks.example
    </li>
    <li>
      <svg viewBox="0 0 24 24"><circle cx="12" cy="12" r="10"/></svg>
      www.bayfieldcapitalworks.example
    </li>
  </ul>
</section>

<section class="card card--back" aria-label="Business card back">
  <div class="back-texture" role="img" aria-label="Subtle tonal navy background texture"></div>
  <div class="back-brand">
    <div class="brand__row">
      <span class="brand__square"></span>
      <span class="brand__name">Bayfield Capital Works, Inc</span>
    </div>
    <div class="brand__tagline">Trusted guidance for every business sale</div>
  </div>
</section>

</body>
</html>
```